vorne matcha

I'm a local business called 'VORNE' and will be sourcing organic ceremonial grade matcha tea through a private labeler in Japan. I need a sleek layout for the label that wraps around the tin that holds the 30g of matcha. I have samples of inspiration and designs that I like. This is very high end matcha so I would like for it to have an expensive look. I also have the dimensions of the label for the tin to show. I have specifics of things that need to be on the label, so please let me know if you need any of that information at this point!

Target Market(s)

High end matcha tea drinkers. The label files I sent are what my eye was drawn to.

Industry/Entity Type

matcha

Font styles to use
Other font styles liked:
• I like the font styles of the samples I uploaded in the photos

Colors

Designer to choose only greyscale colors for use in the design.

Requirements
Must have
• In the biggest lettering of them all in the center is MATCHA. (everything capitalized).Above it, my brand name which is VORNE. and if it looks good, Vorne no.7 like the Duvelle no.5.below the MATCHA, I would like it to say Ceremonial Grade.Another thing... Design wise!I would like the tin to be silver, and the label to be a sort of creme, in between white color with black lettering. Also, I would like the font to be more along the lines of the Ma Verte fonts I sent you... the files that show the cologne bottle with the silver top, creme label, and lettering:)Thanks so much and can't to see what you doOn it as well, the USDA certified organic label, which is in one of the screenshots I uploaded.There needs to be the net weight which is 30g. and also that it is sourced in Uji, Japanmy website on the back: www.saptamatcha.comThe nutrition facts and how to use I will send later:)
Nice to have
• my signature somewhere (like the coffee picture I sent)

```html
<!DOCTYPE html>
<html lang="en">
<head>
<meta charset="utf-8">
<title>Vorne Matcha – Tin Label</title>
<link href="https://fonts.googleapis.com/css2?family=Old+Standard+TT:wght@400;700&family=Space+Mono:wght@400;700&family=Noto+Serif+JP:wght@500&display=swap" rel="stylesheet">
<style>
  :root{
    --paper:#ffffff;
    --label:#ffffff;
    --ink:#2f2f2f;
    --ink-soft:#555555;
    --rule:#6a6a6a;
    --sage:#7f9a63;
    --art:#a9bc92;
    --edge:#d6d6d6;
  }
  *{margin:0;padding:0;box-sizing:border-box}
  html,body{width:1200px;height:1001px;overflow:hidden;background:var(--paper)}
  .sheet{position:relative;width:1200px;height:1001px}
  .label{position:absolute;left:326px;width:568px;height:100px;background:var(--label);
    box-shadow:0 0 0 .5px var(--edge), 0 1px 2px rgba(0,0,0,.12);overflow:hidden;color:var(--ink)}
  .label--1{top:165px}.label--2{top:354px}.label--3{top:543px}.label--4{top:733px}
  .abs{position:absolute}
  .mono{font-family:"Space Mono",monospace}
  .signature-area{left:16px;top:30px;width:20px;height:38px;background:#efefef;border-radius:3px}
  .info{left:36px;width:93px;text-align:center;font-size:3.4px;line-height:4.6px;white-space:nowrap}
  .info--web{top:14px}
  .sourced{left:40px;top:28px;width:43px;height:16px;border:.5px solid var(--rule)}
  .sourced__text{position:absolute;left:2px;top:3px;color:var(--sage);font-size:3.2px;line-height:4.4px;text-align:center;width:30px;white-space:nowrap}
  .sourced__map{position:absolute;right:2px;top:2px;width:8px;height:11px;background:#b9c6ab;border-radius:2px}
  .badge{top:28px;height:16px;background:#3a3a3a}
  .badge--round{left:87px;width:16px;border-radius:50%}
  .badge--pill{left:106px;top:31px;width:20px;height:10px;border-radius:5px;background:none;border:1px solid #3a3a3a}
  .net{top:50px;font-weight:700;font-size:4.4px}
  .serving{top:57px}
  .nutrition{left:36px;top:68px;width:93px;border-top:.6px solid var(--rule);border-bottom:.6px solid var(--rule);
    padding:1.5px 1px;display:grid;grid-template-columns:60px 1fr;font-size:3.2px;line-height:5.6px;white-space:nowrap}
  .tagline{left:172px;top:27px;font-family:"Noto Serif JP",serif;font-size:6.5px;line-height:7px;writing-mode:vertical-rl;text-orientation:upright;color:var(--ink)}
  .art{left:200px;top:0;width:114px;height:100px;background:var(--art);border-radius:0 0 40px 40px}
  .label--1 .art{opacity:.35}.label--2 .art{opacity:.45}.label--3 .art{opacity:.7}.label--4 .art{opacity:.85}
  .brand{left:190px;width:140px;text-align:center;top:24px;font-size:8px;line-height:10px;font-weight:400;color:var(--ink-soft)}
  .product{left:190px;width:140px;text-align:center;top:35px;font-family:"Old Standard TT",serif;font-weight:700;font-size:27px;letter-spacing:.5px;line-height:30px;color:var(--ink)}
  .divider{left:194px;top:66px;width:131px;border-top:.6px dashed var(--rule)}
  .grade{left:190px;width:140px;text-align:center;top:70px;font-weight:700;font-size:9.4px;line-height:13px;letter-spacing:.6px;color:var(--ink)}
  .box{left:391px;width:136px;border:.6px solid var(--rule);font-size:3.2px;line-height:4.9px;padding:1px 4px;overflow:hidden}
  .box__head{font-weight:700;border-bottom:.5px dashed var(--rule);padding-bottom:.5px;margin:0 -3px 1px}
  .box--ingredients{top:8px;height:16px}
  .box--howto{top:28px;height:56px}
  .box ul{list-style:none;text-align:justify}
  .box li{padding-left:3px;text-indent:-3px}
  .box li::before{content:"› "}
  .claims{left:396px;top:88px;font-size:5px;font-weight:700;letter-spacing:.3px;white-space:nowrap}
  .claims .vegan{color:var(--sage)}
</style>
</head>
<body>
<main class="sheet">
  <section class="label label--1">
    <div class="abs signature-area" role="img" aria-label="Space for owner signature"></div>
    <p class="abs info info--web mono">www.vornematcha.com<br>Certified Organic by KAISEI CERT</p>
    <div class="abs sourced mono"><span class="sourced__text">Sourced in<br>Shizuoka,Japan</span><span class="sourced__map" role="img" aria-label="Small map of Japan"></span></div>
    <div class="abs badge badge--round" role="img" aria-label="Organic certification badge"></div>
    <div class="abs badge badge--pill" role="img" aria-label="Organic certification badge"></div>
    <p class="abs info net mono">NET WEIGHT: 30G</p>
    <p class="abs info serving mono">Serving Size: 1/2 teaspoon (1g)<br>Servings per Container: approximately 30</p>
    <div class="abs nutrition mono"><span>›Calories: 0g</span><span>›Total Fat: 0g</span><span>›Total Carbohydrates: 0g</span><span>›Sodium: 0g</span></div>
    <p class="abs tagline">生まれ変わった</p>
    <div class="abs art" role="img" aria-label="Tiger head illustration in sage green"></div>
    <p class="abs brand mono">VORNE</p>
    <h1 class="abs product">MATCHA</h1>
    <div class="abs divider"></div>
    <p class="abs grade mono">CEREMONIAL GRADE</p>
    <div class="abs box box--ingredients mono"><p class="box__head">INGREDIENTS:</p><p>Organic Japanese Green Tea Powder</p></div>
    <div class="abs box box--howto mono"><p class="box__head">HOW TO USE:</p><ul>
      <li>Using a chashaku (bamboo tea scoop), measure 2 scoops (1/2 tsp) into a chawan (tea bowl).</li>
      <li>Add 1/4 cup of simmering water (175 degrees) to chawan.</li>
      <li>Using a chasen (bamboo tea whisk), whisk the matcha and hot water. Hold the chasen vertically and barely touching the bottom of the bowl. Stir slowly until matcha is dissolved. Then briskly whisk back and forth in the middle of the tea bowl until a light foam has developed.</li>
      <li>Send love, give gratitude, and enjoy&lt;3</li></ul></div>
    <p class="abs claims mono"><span class="vegan">VEGAN</span> | GLUTEN FREE | NON GMO</p>
  </section>

  <section class="label label--2">
    <div class="abs signature-area" role="img" aria-label="Space for owner signature"></div>
    <p class="abs info info--web mono">www.vornematcha.com<br>Certified Organic by KAISEI CERT</p>
    <div class="abs sourced mono"><span class="sourced__text">Sourced in<br>Shizuoka,Japan</span><span class="sourced__map" role="img" aria-label="Small map of Japan"></span></div>
    <div class="abs badge badge--round" role="img" aria-label="Organic certification badge"></div>
    <div class="abs badge badge--pill" role="img" aria-label="Organic certification badge"></div>
    <p class="abs info net mono">NET WEIGHT: 30G</p>
    <p class="abs info serving mono">Serving Size: 1/2 teaspoon (1g)<br>Servings per Container: approximately 30</p>
    <div class="abs nutrition mono"><span>›Calories: 0g</span><span>›Total Fat: 0g</span><span>›Total Carbohydrates: 0g</span><span>›Sodium: 0g</span></div>
    <p class="abs tagline">生まれ変わった</p>
    <div class="abs art" role="img" aria-label="Tiger head illustration in sage green"></div>
    <p class="abs brand mono">VORNE</p>
    <h1 class="abs product">MATCHA</h1>
    <div class="abs divider"></div>
    <p class="abs grade mono">CEREMONIAL GRADE</p>
    <div class="abs box box--ingredients mono"><p class="box__head">INGREDIENTS:</p><p>Organic Japanese Green Tea Powder</p></div>
    <div class="abs box box--howto mono"><p class="box__head">HOW TO USE:</p><ul>
      <li>Using a chashaku (bamboo tea scoop), measure 2 scoops (1/2 tsp) into a chawan (tea bowl).</li>
      <li>Add 1/4 cup of simmering water (175 degrees) to chawan.</li>
      <li>Using a chasen (bamboo tea whisk), whisk the matcha and hot water. Hold the chasen vertically and barely touching the bottom of the bowl. Stir slowly until matcha is dissolved. Then briskly whisk back and forth in the middle of the tea bowl until a light foam has developed.</li>
      <li>Send love, give gratitude, and enjoy&lt;3</li></ul></div>
    <p class="abs claims mono"><span class="vegan">VEGAN</span> | GLUTEN FREE | NON GMO</p>
  </section>

  <section class="label label--3">
    <div class="abs signature-area" role="img" aria-label="Space for owner signature"></div>
    <p class="abs info info--web mono">www.vornematcha.com<br>Certified Organic by KAISEI CERT</p>
    <div class="abs sourced mono"><span class="sourced__text">Sourced in<br>Shizuoka,Japan</span><span class="sourced__map" role="img" aria-label="Small map of Japan"></span></div>
    <div class="abs badge badge--round" role="img" aria-label="Organic certification badge"></div>
    <div class="abs badge badge--pill" role="img" aria-label="Organic certification badge"></div>
    <p class="abs info net mono">NET WEIGHT: 30G</p>
    <p class="abs info serving mono">Serving Size: 1/2 teaspoon (1g)<br>Servings per Container: approximately 30</p>
    <div class="abs nutrition mono"><span>›Calories: 0g</span><span>›Total Fat: 0g</span><span>›Total Carbohydrates: 0g</span><span>›Sodium: 0g</span></div>
    <p class="abs tagline">生まれ変わった</p>
    <div class="abs art" role="img" aria-label="Tiger head illustration in sage green"></div>
    <p class="abs brand mono">VORNE</p>
    <h1 class="abs product">MATCHA</h1>
    <div class="abs divider"></div>
    <p class="abs grade mono">CEREMONIAL GRADE</p>
    <div class="abs box box--ingredients mono"><p class="box__head">INGREDIENTS:</p><p>Organic Japanese Green Tea Powder</p></div>
    <div class="abs box box--howto mono"><p class="box__head">HOW TO USE:</p><ul>
      <li>Using a chashaku (bamboo tea scoop), measure 2 scoops (1/2 tsp) into a chawan (tea bowl).</li>
      <li>Add 1/4 cup of simmering water (175 degrees) to chawan.</li>
      <li>Using a chasen (bamboo tea whisk), whisk the matcha and hot water. Hold the chasen vertically and barely touching the bottom of the bowl. Stir slowly until matcha is dissolved. Then briskly whisk back and forth in the middle of the tea bowl until a light foam has developed.</li>
      <li>Send love, give gratitude, and enjoy&lt;3</li></ul></div>
    <p class="abs claims mono"><span class="vegan">VEGAN</span> | GLUTEN FREE | NON GMO</p>
  </section>

  <section class="label label--4">
    <div class="abs signature-area" role="img" aria-label="Space for owner signature"></div>
    <p class="abs info info--web mono">www.vornematcha.com<br>Certified Organic by KAISEI CERT</p>
    <div class="abs sourced mono"><span class="sourced__text">Sourced in<br>Shizuoka,Japan</span><span class="sourced__map" role="img" aria-label="Small map of Japan"></span></div>
    <div class="abs badge badge--round" role="img" aria-label="Organic certification badge"></div>
    <div class="abs badge badge--pill" role="img" aria-label="Organic certification badge"></div>
    <p class="abs info net mono">NET WEIGHT: 30G</p>
    <p class="abs info serving mono">Serving Size: 1/2 teaspoon (1g)<br>Servings per Container: approximately 30</p>
    <div class="abs nutrition mono"><span>›Calories: 0g</span><span>›Total Fat: 0g</span><span>›Total Carbohydrates: 0g</span><span>›Sodium: 0g</span></div>
    <p class="abs tagline">生まれ変わった</p>
    <div class="abs art" role="img" aria-label="Tiger head illustration in sage green"></div>
    <p class="abs brand mono">VORNE</p>
    <h1 class="abs product">MATCHA</h1>
    <div class="abs divider"></div>
    <p class="abs grade mono">CEREMONIAL GRADE</p>
    <div class="abs box box--ingredients mono"><p class="box__head">INGREDIENTS:</p><p>Organic Japanese Green Tea Powder</p></div>
    <div class="abs box box--howto mono"><p class="box__head">HOW TO USE:</p><ul>
      <li>Using a chashaku (bamboo tea scoop), measure 2 scoops (1/2 tsp) into a chawan (tea bowl).</li>
      <li>Add 1/4 cup of simmering water (175 degrees) to chawan.</li>
      <li>Using a chasen (bamboo tea whisk), whisk the matcha and hot water. Hold the chasen vertically and barely touching the bottom of the bowl. Stir slowly until matcha is dissolved. Then briskly whisk back and forth in the middle of the tea bowl until a light foam has developed.</li>
      <li>Send love, give gratitude, and enjoy&lt;3</li></ul></div>
    <p class="abs claims mono"><span class="vegan">VEGAN</span> | GLUTEN FREE | NON GMO</p>
  </section>
</main>
</body>
</html>
```